Business Card Design

I already have a company logo for my company. I have a logo for the manufacturer we represent. I want a professional business card design.

```html
<!DOCTYPE html>
<html lang="en">
<head>
<meta charset="utf-8">
<title>Halvern Alert — Business Card</title>
<link href="https://fonts.googleapis.com/css2?family=Open+Sans:wght@400;600;700&display=swap" rel="stylesheet">
<style>
  :root {
    --stage: #232323;
    --card: #f4f4f4;
    --red: #e31e24;
    --gold: #c29a2e;
    --ink: #1f1f1f;
    --shade: #9a9a9a;
  }
  * { margin: 0; padding: 0; box-sizing: border-box; }
  html, body { width: 1200px; height: 780px; overflow: hidden; }
  body {
    background: var(--stage);
    font-family: "Open Sans", Arial, sans-serif;
    position: relative;
  }
  .card {
    position: absolute;
    width: 525px;
    height: 300px;
    background: var(--card);
    border-radius: 2px;
    box-shadow: 0 10px 24px rgba(0,0,0,.45);
    overflow: hidden;
    top: 240px;
  }
  .card--front { left: 50px; }
  .card--back { left: 625px; }

  .front__swoosh { position: absolute; left: 0; top: 0; }

  .holder {
    position: absolute;
    left: 44px;
    top: 50px;
  }
  .holder__name {
    font-size: 30px;
    font-weight: 700;
    font-style: italic;
    line-height: 1.1;
    letter-spacing: -0.3px;
  }
  .holder__first { color: var(--red); }
  .holder__last { color: var(--gold); }
  .holder__title {
    font-size: 14px;
    font-weight: 600;
    color: var(--ink);
    margin-left: 96px;
    margin-top: 2px;
  }
  .address {
    position: absolute;
    left: 44px;
    bottom: 60px;
    font-size: 13.5px;
    font-weight: 600;
    color: var(--ink);
  }
  .contacts {
    position: absolute;
    left: 290px;
    top: 138px;
    list-style: none;
  }
  .contacts__item {
    display: flex;
    align-items: center;
    gap: 8px;
    font-size: 14px;
    font-weight: 600;
    color: var(--ink);
    line-height: 24px;
  }
  .contacts__icon { width: 14px; height: 14px; flex: none; }

  .brand {
    position: absolute;
    right: 40px;
    bottom: 38px;
    display: flex;
    align-items: center;
    gap: 10px;
  }
  .brand__dot {
    width: 26px;
    height: 26px;
    border-radius: 50%;
    background: var(--red);
  }
  .brand__name {
    font-size: 26px;
    font-weight: 700;
    color: var(--red);
    letter-spacing: 0.5px;
  }
</style>
</head>
<body>

  <section class="card card--front" aria-label="Business card front">
    <svg class="front__swoosh" width="525" height="300" viewBox="0 0 525 300" aria-hidden="true">
      <defs>
        <linearGradient id="swoosh-shade" x1="0" y1="1" x2="1" y2="0">
          <stop offset="0" stop-color="#f4f4f4" stop-opacity="0"/>
          <stop offset="0.55" stop-color="#b5b5b5" stop-opacity="0.55"/>
          <stop offset="1" stop-color="#f4f4f4" stop-opacity="0"/>
        </linearGradient>
      </defs>
      <path d="M190 250 C260 190 330 120 400 100 C440 90 470 110 450 140 C400 170 330 220 270 260 Z" fill="url(#swoosh-shade)"/>
    </svg>

    <div class="holder">
      <p class="holder__name"><span class="holder__first">Lenka</span> <span class="holder__last">Marsalova</span></p>
      <p class="holder__title">Managing Director</p>
    </div>

    <ul class="contacts">
      <li class="contacts__item">
        <svg class="contacts__icon" viewBox="0 0 16 16" aria-hidden="true">
          <circle cx="8" cy="8" r="8" fill="var(--red)"/>
          <path d="M5 4.5 l1.6-.4 .8 2-1 .8 a5 5 0 0 0 2.7 2.7 l.8-1 2 .8 -.4 1.6 a6.5 6.5 0 0 1 -6.5-6.5z" fill="#fff"/>
        </svg>
        (555) 014-2290
      </li>
      <li class="contacts__item">
        <svg class="contacts__icon" viewBox="0 0 16 16" aria-hidden="true">
          <circle cx="8" cy="8" r="8" fill="var(--red)"/>
          <rect x="4" y="5" width="8" height="6" fill="none" stroke="#fff" stroke-width="1.2"/>
          <path d="M4 5 L8 8.5 L12 5" fill="none" stroke="#fff" stroke-width="1.2"/>
        </svg>
        hello@halvernalert.com
      </li>
      <li class="contacts__item">
        <svg class="contacts__icon" viewBox="0 0 16 16" aria-hidden="true">
          <circle cx="8" cy="8" r="8" fill="var(--red)"/>
          <circle cx="8" cy="8" r="4.5" fill="none" stroke="#fff" stroke-width="1.1"/>
          <path d="M3.5 8 H12.5 M8 3.5 C6 6 6 10 8 12.5 M8 3.5 C10 6 10 10 8 12.5" fill="none" stroke="#fff" stroke-width="1"/>
        </svg>
        www.halvernalert.com
      </li>
    </ul>

    <p class="address">4810 Cedar Ridge Rd. Suite 300 Alder Falls, TX 75990</p>
  </section>

  <section class="card card--back" aria-label="Business card back">
    <div class="brand">
      <span class="brand__dot" aria-hidden="true"></span>
      <span class="brand__name">Halvern Alert</span>
    </div>
  </section>

</body>
</html>
```